Whitcombe Business Card Design

The name of the business is Dario Whitcombe, CPA LLC
The service that we offer is Accounting, Tax & Consulting Services. I need it to have the following items:
Dario Whitcombe, Principal
Phone Number
Email Address
Physical Address

I have attached the company logo, one in black and one in white. Please provide a design in black background and the other in white background. Please include "Accounting, Tax & Consulting Services". I want the business card to be clean and very professional.

```html
<!DOCTYPE html>
<html lang="en">
<head>
<meta charset="utf-8">
<title>Dario Whitcombe, CPA LLC — Business Cards</title>
<link href="https://fonts.googleapis.com/css2?family=Montserrat:wght@400;500&family=Open+Sans:wght@400&display=swap" rel="stylesheet">
<style>
  :root {
    --stage: #2b2b2b;
    --card-light: #e9eaeb;
    --card-dark: #141415;
    --red: #a01e22;
    --charcoal: #414042;
    --slate: #58595b;
    --slate-light: #6d6e70;
    --grey-text: #7a7b7d;
    --grey-soft: #b5b6b8;
    --white: #ffffff;
  }
  * { box-sizing: border-box; margin: 0; padding: 0; }
  html, body { width: 1200px; height: 1200px; overflow: hidden; }
  body {
    background: var(--stage);
    font-family: "Montserrat", sans-serif;
    position: relative;
  }
  .card {
    position: absolute;
    left: 150px;
    width: 900px;
    height: 514px;
    overflow: hidden;
  }
  .card--front { top: 70px; background: var(--card-light); }
  .card--back { top: 616px; background: var(--card-dark); }

  .card__bands { position: absolute; left: 0; bottom: 0; width: 900px; height: 70px; }

  /* Front (white background) */
  .person { position: absolute; left: 54px; top: 84px; }
  .person__name {
    font-size: 28px; font-weight: 500; letter-spacing: 0.5px;
    color: var(--charcoal); line-height: 1;
  }
  .person__first { color: var(--red); }
  .person__role { font-size: 19px; color: var(--charcoal); margin-top: 16px; }
  .person__rule { width: 90px; height: 3px; background: var(--red); margin-top: 10px; }

  .firm__name {
    font-size: 24px; font-weight: 500; color: var(--charcoal);
    letter-spacing: 0.3px; line-height: 1;
  }
  .firm__tagline {
    font-size: 15px; color: var(--grey-text); letter-spacing: 2px;
    margin-top: 9px; text-transform: uppercase;
  }
  .card--front .firm { position: absolute; right: 40px; top: 78px; text-align: right; }

  .firm-square { position: absolute; background: var(--charcoal); }
  .card--front .firm-square { left: 660px; top: 274px; width: 135px; height: 135px; }

  .contacts { position: absolute; left: 54px; top: 292px; list-style: none; }
  .contact { display: flex; align-items: center; height: 38px; margin-bottom: 22px; }
  .contact__icon {
    width: 38px; height: 38px; border-radius: 50%; background: var(--red);
    display: flex; align-items: center; justify-content: center; flex-shrink: 0;
  }
  .contact__text {
    margin-left: 19px; font-family: "Open Sans", sans-serif;
    font-size: 14px; line-height: 1.3; color: var(--slate);
  }

  /* Back (black background) */
  .card--back .firm-square { left: 393px; top: 108px; width: 114px; height: 114px; background: var(--card-light); }
  .card--back .firm { position: absolute; left: 0; right: 0; top: 252px; text-align: center; }
  .card--back .firm__name { font-size: 28px; color: var(--white); }
  .card--back .firm__tagline { font-size: 17px; margin-top: 10px; color: var(--grey-soft); }

  .services {
    position: absolute; left: 18px; bottom: 32px;
    font-family: "Open Sans", sans-serif;
    font-size: 19px; color: var(--white); line-height: 1;
  }
</style>
</head>
<body>

  <section class="card card--front" aria-label="Business card front, white background">
    <div class="person">
      <p class="person__name"><span class="person__first">DARIO</span> WHITCOMBE</p>
      <p class="person__role">Principal</p>
      <div class="person__rule"></div>
    </div>

    <div class="firm">
      <p class="firm__name">Dario Whitcombe, CPA LLC</p>
      <p class="firm__tagline">Certified Public Accountant</p>
    </div>

    <div class="firm-square"></div>

    <ul class="contacts">
      <li class="contact">
        <span class="contact__icon">
          <svg width="18" height="18" viewBox="0 0 24 24" fill="none" stroke="#fff" stroke-width="1.8" stroke-linecap="round" stroke-linejoin="round"><path d="M22 16.9v3a2 2 0 0 1-2.2 2 19.8 19.8 0 0 1-8.6-3.1 19.5 19.5 0 0 1-6-6A19.8 19.8 0 0 1 2.1 4.2 2 2 0 0 1 4.1 2h3a2 2 0 0 1 2 1.7c.1 1 .4 1.9.7 2.8a2 2 0 0 1-.5 2.1L8 9.9a16 16 0 0 0 6 6l1.3-1.3a2 2 0 0 1 2.1-.4c.9.3 1.8.6 2.8.7a2 2 0 0 1 1.7 2z"/></svg>
        </span>
        <span class="contact__text">+1 (555) 013 2074<br>+1 (555) 068 4599</span>
      </li>
      <li class="contact">
        <span class="contact__icon">
          <svg width="18" height="18" viewBox="0 0 24 24" fill="none" stroke="#fff" stroke-width="1.8" stroke-linejoin="round"><rect x="3" y="5" width="18" height="14" rx="1"/><path d="M3 6l9 7 9-7"/></svg>
        </span>
        <span class="contact__text">info@whitcombecpa.com</span>
      </li>
      <li class="contact">
        <span class="contact__icon">
          <svg width="18" height="18" viewBox="0 0 24 24" fill="none" stroke="#fff" stroke-width="1.8" stroke-linejoin="round"><path d="M12 22s7-6.6 7-12a7 7 0 0 0-14 0c0 5.4 7 12 7 12z"/><circle cx="12" cy="10" r="2.5"/></svg>
        </span>
        <span class="contact__text">1450 Meridian Avenue, Suite 210<br>Springfield, IL 62701</span>
      </li>
    </ul>

    <svg class="card__bands" viewBox="0 0 900 70" preserveAspectRatio="none" aria-hidden="true">
      <rect x="0" y="19" width="460" height="11" fill="var(--slate)"/>
      <polygon points="485,9 900,9 900,43 460,43" fill="var(--charcoal)"/>
      <rect x="0" y="43" width="900" height="27" fill="var(--red)"/>
    </svg>
  </section>

  <section class="card card--back" aria-label="Business card back, black background">
    <div class="firm-square"></div>
    <div class="firm">
      <p class="firm__name">Dario Whitcombe, CPA LLC</p>
      <p class="firm__tagline">Certified Public Accountant</p>
    </div>

    <svg class="card__bands" viewBox="0 0 900 70" preserveAspectRatio="none" aria-hidden="true">
      <polygon points="0,5 415,5 440,43 0,43" fill="var(--slate)"/>
      <rect x="425" y="20" width="475" height="12" fill="var(--slate-light)"/>
      <rect x="0" y="43" width="900" height="27" fill="var(--red)"/>
    </svg>
    <p class="services">Accounting, Tax &amp; Consulting Services</p>
  </section>

</body>
</html>
```